Brand new letterhead, business card, email signature etc.

We are a financial company in London, UK. Our website is www.marlowvane.com. We're wanting a complete remodel of the company colours, letter head, business cards, email signatures, etc. Looking to keep the same font for the company name. I have upload a colour palette that we want to work with. We're looking for company letterhead for outgoing letters/ correspondence, letterhead for internal documentation, email signatures, e-letters. etc. Ultimately we will redesign the entire website also. It is important that our clients get a strong, secure, warm, trustworthy, solid feeling and first impression.
Updates

Designs look the same

Target Market(s)

Institutional investors, (ultra) high net worth individuals

Industry/Entity Type

Finance, Invesments banking.

Font styles to use
Other font styles liked:
• Current font is "Champagne & Limousines"

Requirements
Must have
• Must use the colours provided on the PDF uploaded to the portal. The purple = main colour. The red = accent colour.
Nice to have
• Nice to use same font as now for the company name "Corvane". Font is "Champagne & Limousines". Nice to have some reference to the old logo flower, but only subtle.
Should not have
• Do not use the colour red from our website. Use the colours provided on the colour palette PDF that I uploaded in the portal.

```html
<!DOCTYPE html>
<html lang="en">
<head>
<meta charset="utf-8">
<title>Corvane Letterhead</title>
<link href="https://fonts.googleapis.com/css2?family=Josefin+Sans:wght@300&family=Montserrat:wght@400;500&display=swap" rel="stylesheet">
<style>
  :root {
    --backdrop: #eeeeee;
    --paper: #ffffff;
    --ink: #3a3a3a;
    --ink-soft: #555555;
    --brand-purple: #3a1a2e;
    --accent-red: #d8432a;
    --signature-blue: #2a3fbf;
    --band-text: #f2eef0;
  }
  * { box-sizing: border-box; margin: 0; padding: 0; }
  html, body { width: 1200px; height: 900px; overflow: hidden; }
  body {
    background: var(--backdrop);
    font-family: "Montserrat", Arial, sans-serif;
    color: var(--ink);
  }
  .letterhead {
    position: absolute;
    left: 300px;
    top: 26px;
    width: 600px;
    height: 848px;
    background: var(--paper);
    box-shadow: 0 2px 10px rgba(0,0,0,0.08);
  }
  .brand-name {
    position: absolute;
    top: 64px;
    right: 64px;
    font-family: "Josefin Sans", Arial, sans-serif;
    font-weight: 300;
    font-size: 22px;
    letter-spacing: 6px;
    text-transform: uppercase;
    color: var(--ink);
  }
  .letter-body {
    position: absolute;
    left: 64px;
    top: 300px;
    width: 420px;
    font-size: 9.4px;
    line-height: 1.5;
    color: var(--ink-soft);
  }
  .letter-body p { margin-bottom: 11px; }
  .signature {
    position: absolute;
    left: 64px;
    top: 604px;
  }
  .signature-mark { display: block; width: 130px; height: 34px; }
  .signatory-role {
    font-size: 10px;
    margin-top: 2px;
    color: var(--ink);
  }
  .address {
    position: absolute;
    right: 64px;
    top: 660px;
    text-align: right;
    font-size: 9px;
    line-height: 1.45;
    color: var(--ink-soft);
  }
  .footer-rule {
    position: absolute;
    left: 0; right: 0;
    bottom: 60px;
    height: 4px;
    background: var(--accent-red);
  }
  .footer-band {
    position: absolute;
    left: 0; right: 0; bottom: 0;
    height: 56px;
    background: var(--brand-purple);
  }
  .website {
    position: absolute;
    right: 64px;
    top: 12px;
    font-size: 9px;
    color: var(--band-text);
    letter-spacing: 0.3px;
  }
</style>
</head>
<body>
  <main class="letterhead">
    <div class="brand-name">Corvane</div>

    <section class="letter-body">
      <p>Letterhead samples are a great way of deciding what kind of letterhead you want to design for you and your company. The internet has a ton of great letterhead samples to browse through. Whether you want something simple, with just a couple lines of text or your business information or something decorative and stunning, with photos and logos on the top and bottom of the page, it will be easy to find what you want, because there are samples online for basically any type of letterhead you could want.</p>
      <p>Any business could easily benefit from browsing through some letterhead samples, if only to get an idea for what kind of letterhead their company might want. Letterheads are just one of the tools that a business professional could use to help increase their customer base, and to really be memorable to everyone they write a letter to. Letterhead is quite an effective tool for marketing and advertising, but because it&rsquo;s such a simple and well known idea, it is often unfairly overlooked. Make sure you don&rsquo;t make that mistake, and make some letterhead samples of your own today.</p>
      <p>Whether you want to get new customers to remember you and become part of your clientele, or you just want to send out friendly reminders to your existing clients, customizing your own letterhead samples can really help you out. Try out some letterhead samples and you will not regret it, and I&rsquo;m sure you will add a new tool to your business&rsquo; arsenal of networking, marketing, and advertising tools.</p>
    </section>

    <div class="signature">
      <svg class="signature-mark" viewBox="0 0 130 34" role="img" aria-label="Handwritten signature of Edmund Harrow in blue ink">
        <defs>
          <linearGradient id="ink-wash" x1="0" x2="1">
            <stop offset="0" stop-color="var(--signature-blue)" stop-opacity="0.35"/>
            <stop offset="1" stop-color="var(--signature-blue)" stop-opacity="0.12"/>
          </linearGradient>
        </defs>
        <rect x="0" y="8" width="130" height="20" rx="10" fill="url(#ink-wash)"/>
      </svg>
      <div class="signatory-role">company director</div>
    </div>

    <address class="address" style="font-style: normal;">
      18 Hollis Yard<br>
      EC2M 7PQ, London<br>
      United Kingdom
    </address>

    <div class="footer-rule"></div>
    <footer class="footer-band">
      <span class="website">www.marlowvane.com</span>
    </footer>
  </main>
</body>
</html>
```